Bry7Legal Letterhead

Need a new letterhead for my law firm.
IDENTIFYING INFORMATION BELOW:
Anselmo R Quintara III
Attorney at Law
Address: 2847 Larkspur Blvd, Ste 300, Dallas, TX 75204
Phone: 877-482-6017
Fax: 469-738-1452
Email: bry@bry7legal.example
Website: www.bry7legal.example

Colors
0054AA
0677BA
7BADD7
CADEEF
E8F1F8

Requirements
Must have
• Logo needs to be on the letterhead, along with identifying information which is included in the project description.

```html
<!DOCTYPE html>
<html lang="en">
<head>
<meta charset="utf-8">
<title>Bry7Legal Letterhead</title>
<link rel="stylesheet" href="https://fonts.googleapis.com/css2?family=Open+Sans:wght@400;700&display=swap">
<style>
  :root {
    --backdrop: #d9dcde;
    --paper: #ffffff;
    --ink: #0a0a0a;
    --brand-blue: #0677ba;
    --text-grey: #555a5e;
    --on-dark: #ffffff;
  }
  * { box-sizing: border-box; margin: 0; padding: 0; }
  html, body { width: 1200px; height: 784px; overflow: hidden; }
  body {
    background: var(--backdrop);
    font-family: "Open Sans", Arial, sans-serif;
    position: relative;
  }
  .letterhead {
    position: absolute;
    left: 320px; top: 30px;
    width: 560px; height: 724px;
    background: var(--paper);
    box-shadow: 0 6px 18px rgba(0,0,0,0.18);
    overflow: hidden;
  }
  .firm-name {
    position: absolute; left: 38px; top: 14px;
    font-family: "Open Sans", Arial, sans-serif;
    font-weight: 700; font-size: 24px;
    color: var(--ink); line-height: 1;
  }
  .firm-tagline {
    position: absolute; left: 39px; top: 44px;
    font-size: 9.5px; letter-spacing: 1.6px; color: var(--ink);
  }
  .attorney-band {
    position: absolute; right: 0; top: 62px;
    width: 340px; height: 36px;
  }
  .attorney-band svg { position: absolute; inset: 0; }
  .attorney-name, .attorney-title {
    position: absolute; right: 14px; color: var(--on-dark); text-align: right; white-space: nowrap;
  }
  .attorney-name { top: 7px; font-weight: 700; font-size: 9px; letter-spacing: .3px; }
  .attorney-title { top: 20px; font-size: 7px; letter-spacing: .6px; }
  .footer-contact {
    position: absolute; left: 10px; bottom: 44px;
    font-size: 8.5px; color: var(--text-grey); white-space: nowrap;
    display: flex; align-items: center; gap: 5px;
  }
  .footer-contact svg { width: 8px; height: 8px; fill: var(--ink); }
  .footer-rules { position: absolute; left: 0; bottom: 0; width: 560px; height: 42px; }
  .footer-web {
    position: absolute; right: 16px; bottom: 9px;
    font-weight: 700; font-size: 12.5px; color: var(--on-dark); white-space: nowrap;
  }
</style>
</head>
<body>
  <main class="letterhead">
    <div class="firm-name">Bry7Legal</div>
    <div class="firm-tagline">STAND WITH BRY7</div>

    <div class="attorney-band">
      <svg viewBox="0 0 340 36" preserveAspectRatio="none"><polygon points="12,0 340,0 340,36 0,36" fill="var(--ink)"/></svg>
      <div class="attorney-name">ANSELMO R QUINTARA III</div>
      <div class="attorney-title">ATTORNEY AT LAW</div>
    </div>

    <div class="footer-contact">
      <svg viewBox="0 0 10 10"><path d="M5 0a3.5 3.5 0 0 0-3.5 3.5C1.5 6 5 10 5 10s3.5-4 3.5-6.5A3.5 3.5 0 0 0 5 0zm0 5a1.4 1.4 0 1 1 0-2.8A1.4 1.4 0 0 1 5 5z"/></svg>
      <span>2847 Larkspur Blvd, Ste 300, Dallas, TX 75204</span>
      <svg viewBox="0 0 10 10"><path d="M2 0.5l2 2-1 1.3a6 6 0 0 0 3.2 3.2l1.3-1 2 2-1.3 1.5C4.5 9.5.5 5.5.5 1.8z"/></svg>
      <span>877-482-6017</span>
      <svg viewBox="0 0 10 10"><rect x="2" y="0" width="6" height="3"/><rect x="0" y="3.5" width="10" height="4.5" rx="1"/><rect x="2" y="7" width="6" height="3"/></svg>
      <span>469-738-1452</span>
      <svg viewBox="0 0 10 10"><rect x="0" y="1.5" width="10" height="7" rx="1"/></svg>
      <span>bry@bry7legal.example</span>
    </div>

    <svg class="footer-rules" viewBox="0 0 560 42">
      <rect x="0" y="6" width="94" height="4" fill="var(--brand-blue)"/>
      <rect x="98" y="10" width="122" height="4" fill="var(--ink)"/>
      <rect x="224" y="6" width="166" height="4" fill="var(--brand-blue)"/>
      <polygon points="388,12 560,12 560,42 370,42" fill="var(--ink)"/>
      <rect x="0" y="34" width="560" height="8" fill="var(--ink)"/>
    </svg>
    <div class="footer-web">www.bry7legal.example</div>
  </main>
</body>
</html>
```